Haulage company, lets use ruby red white and some 3rd color for web design. and Garvel Pryce Transport logo

Target Market(s)

Transport industry

Industry/Entity Type

transport

Number of Pages Required

2 page

Requirements
Must have
• Logo

```html
<!DOCTYPE html>
<html lang="en">
<head>
<meta charset="utf-8">
<title>Garvel Pryce Transport</title>
<link href="https://fonts.googleapis.com/css2?family=Montserrat:wght@700;800&family=Mulish:wght@400;500;600;700;800&display=swap" rel="stylesheet">
<style>
:root{
  --ruby:#7c0f24;
  --ruby-deep:#6a0a1c;
  --ink:#1b1b1f;
  --text:#4a4a52;
  --blue:#1f5aa6;
  --paper:#ffffff;
  --mist:#f3f2f5;
  --line:#d8d4da;
}
*{box-sizing:border-box;margin:0;padding:0}
html,body{width:1200px;height:4046px;overflow:hidden;background:var(--paper)}
body{position:relative;font-family:'Mulish',sans-serif;color:var(--text)}
.abs{position:absolute}
.head{font-family:'Montserrat',sans-serif;font-weight:800;color:var(--ink);text-transform:uppercase}
.rule{position:absolute;height:3px;width:76px;background:var(--ruby)}
.btn{position:absolute;display:flex;align-items:center;justify-content:center;gap:10px;background:var(--ruby);color:#fff;font-family:'Mulish',sans-serif;font-weight:800;font-size:15px;text-transform:uppercase;letter-spacing:.2px}
.photo{position:absolute}
.para{font-size:14px;line-height:21px;text-align:justify;color:var(--text)}

/* header */
.brand{position:absolute;font-family:'Mulish',sans-serif;font-weight:700;color:var(--ruby);text-transform:uppercase;line-height:1}
.brand .l1{display:block;font-size:31px;letter-spacing:1px}
.brand .l2{display:block;font-size:26px;letter-spacing:6px;margin-top:12px}
.contact-chip{position:absolute;display:flex;align-items:center;gap:12px}
.contact-chip .lbl{font-size:12px;font-weight:700;color:var(--ink);text-transform:uppercase}
.contact-chip .val{font-size:17px;font-weight:700;color:var(--ruby);margin-top:2px}
.nav{position:absolute;left:576px;top:90px;display:flex;gap:0;font-size:15px;font-weight:500;color:var(--ink);text-transform:uppercase}
.nav a{display:block;padding:6px 10px;text-decoration:none;color:inherit;margin-right:17px}
.nav a.on{border:2px solid var(--ruby);color:var(--ruby);font-weight:700}

/* services */
.card{position:absolute;top:1442px;width:299px;height:482px;background:#fff}
.card h3{position:absolute;left:35px;top:38px;font-size:19px;line-height:27px;font-weight:500;color:var(--ink);text-transform:uppercase}
.card h3 b{color:var(--ruby);font-weight:800}
.card p{position:absolute;left:35px;top:98px;width:240px;font-size:12px;line-height:17px;color:var(--text)}
.card .btn{left:35px;top:172px;width:108px;height:34px;font-size:13px}
.card .badge{position:absolute;right:-3px;top:-13px;width:74px;height:74px;border-radius:50%;background:var(--blue);display:flex;align-items:center;justify-content:center}
.card .pic{position:absolute;left:0;top:245px;width:299px;height:237px}

/* accordion */
.acc{position:absolute;left:603px;width:466px;height:47px;border:1.5px solid var(--ruby);display:flex;align-items:center;padding-left:14px;font-size:15px;color:var(--ink)}
.acc svg.ic{width:28px;height:28px;margin-right:16px}
.acc .plus{position:absolute;right:24px;top:12px;width:16px;height:16px}

/* footer */
.ft-h{position:absolute;font-size:14px;font-weight:800;color:#fff;text-transform:uppercase}
.ft-u{position:absolute;height:2px;background:#fff}
.ft-item{position:absolute;display:flex;align-items:flex-start;gap:12px;font-size:12px;line-height:16px;color:#fff}
.ft-dot{width:24px;height:24px;border-radius:50%;background:#fff;flex:none;display:flex;align-items:center;justify-content:center}
.menu{position:absolute;left:746px;top:3776px;font-size:12px;line-height:19px;color:#fff}
</style>
</head>
<body>

<!-- Header -->
<div class="brand" style="left:132px;top:32px"><span class="l1">Garvel Pryce</span><span class="l2">Transport</span></div>

<div class="contact-chip" style="left:570px;top:30px">
  <svg width="32" height="32" viewBox="0 0 32 32"><circle cx="16" cy="16" r="16" fill="var(--ruby)"/><rect x="8" y="10.5" width="16" height="11" rx="1" fill="none" stroke="#fff" stroke-width="1.8"/><path d="M8.5 11.5 16 17l7.5-5.5" fill="none" stroke="#fff" stroke-width="1.8"/></svg>
  <div><div class="lbl">Email Us</div><div class="val">info@garvelprycetransport.com</div></div>
</div>
<div class="contact-chip" style="left:893px;top:30px">
  <svg width="32" height="32" viewBox="0 0 32 32"><circle cx="16" cy="16" r="16" fill="var(--ruby)"/><path d="M11 8.5c1-.6 2 0 2.5 1l1.2 2.4c.4.8.1 1.6-.6 2.1l-1 .7c.9 2 2.3 3.6 4.3 4.5l.8-1c.6-.7 1.4-.9 2.2-.4l2.3 1.3c.9.5 1.2 1.6.6 2.5-1 1.6-2.6 2.3-4.4 1.7-4.7-1.6-8.2-5.4-9.5-10.2-.4-1.5.3-3.7 1.6-4.6z" fill="#fff"/></svg>
  <div><div class="lbl">Call Us</div><div class="val">+1 555 014 2290</div></div>
</div>

<nav class="nav">
  <a class="on" href="#">Home</a><a href="#">About Us</a><a href="#">Services</a><a href="#">Team</a><a href="#">Contact Us</a>
</nav>

<!-- Hero -->
<section class="abs" style="left:0;top:149px;width:1200px;height:564px">
  <div class="photo" role="img" aria-label="Two refrigerated lorries driving along a coastal road beside the sea" style="inset:0;background:linear-gradient(180deg,#8fb0d0 0%,#3d5e80 22%,#767c84 45%,#55585c 72%,#4f6a3c 100%)"></div>
  <div class="abs" style="inset:0;background:linear-gradient(90deg,rgba(0,0,0,.35),rgba(0,0,0,0) 60%)"></div>
  <h1 class="head abs" style="left:132px;top:250px;font-size:40px;line-height:45px;color:#fff">Safe and<br>efficient goods<br>moving with our<br>haulage service</h1>
  <a class="btn" style="left:132px;top:454px;width:141px;height:46px;border:2px solid #fff">Read More</a>
  <svg class="abs" style="left:965px;top:466px" width="40" height="40" viewBox="0 0 40 40"><circle cx="20" cy="20" r="18" fill="var(--ruby)" stroke="#fff" stroke-width="2"/><path d="M28 20H12m6-6-6 6 6 6" fill="none" stroke="#fff" stroke-width="2.2"/></svg>
  <svg class="abs" style="left:1025px;top:466px" width="40" height="40" viewBox="0 0 40 40"><circle cx="20" cy="20" r="18" fill="var(--ruby)" stroke="#fff" stroke-width="2"/><path d="M12 20h16m-6-6 6 6-6 6" fill="none" stroke="#fff" stroke-width="2.2"/></svg>
</section>

<!-- Welcome -->
<div class="photo" role="img" aria-label="Two white and red lorries parked on a yard under a pale sky" style="left:132px;top:770px;width:474px;height:441px;background:linear-gradient(180deg,#b9cde0 0%,#dfe6ec 45%,#9aa0a4 75%,#c7c8c6 100%)"></div>
<h2 class="head abs" style="left:652px;top:795px;font-size:29px;line-height:42px">Welcome to<br><span style="color:var(--ruby)">Garvel Pryce Transport</span></h2>
<div class="rule" style="left:652px;top:898px"></div>
<p class="para abs" style="left:652px;top:942px;width:416px">Sed ut perspiciatis unde omnis iste natus error sit voluptatem accusantium doloremque laudantium, totam rem aperiam, eaque ipsa quae ab illo inventore veritatis et quasi architecto beatae vitae dicta sunt explicabo. Nemo enim ipsam volup tatem quia voluptas sit aspernatur aut odit aut fugit, sed quia consequuntur magni dolores eos qui ratione voluptatem sequi nesciunt. Neque porro quisquam est, qui dolorem ipsum quia dolor sit amet, consectetur, adipisci velit</p>
<a class="btn" style="left:652px;top:1142px;width:191px;height:43px">
  <svg width="26" height="16" viewBox="0 0 26 16"><path d="M1 2h14v10H1zM15 5h5l4 4v3h-9z" fill="#fff"/><circle cx="6" cy="13" r="2.5" fill="#fff" stroke="var(--ruby)"/><circle cx="19" cy="13" r="2.5" fill="#fff" stroke="var(--ruby)"/></svg>More About Us</a>

<!-- Services -->
<section class="abs" style="left:0;top:1271px;width:1200px;height:721px;background:var(--mist)">
  <h2 class="head abs" style="left:0;width:1200px;text-align:center;top:50px;font-size:29px">Our Services</h2>
  <div class="rule" style="left:571px;top:109px;width:58px"></div>
</section>

<div class="card" style="left:113px">
  <div class="badge"><svg width="40" height="28" viewBox="0 0 40 28"><path d="M2 4h22v16H2zM24 9h8l6 7v4H24z" fill="#fff"/><circle cx="10" cy="22" r="4" fill="#fff" stroke="var(--blue)" stroke-width="2"/><circle cx="31" cy="22" r="4" fill="#fff" stroke="var(--blue)" stroke-width="2"/></svg></div>
  <h3><b>Haulage &amp;</b><br>Transportation</h3>
  <p>Sed ut perspiciatis unde omnis iste natus error sit voluptatem accusantium dolore mque laudantium.</p>
  <a class="btn">Read More</a>
  <div class="pic" role="img" aria-label="White lorry with red cab trim parked beside a trailer" style="background:linear-gradient(180deg,#9fbbd6 0%,#dce3e8 40%,#b08a8f 70%,#8c8f90 100%)"></div>
  <svg class="abs" style="left:0;top:1873px;top:431px" width="299" height="52" viewBox="0 0 299 52"><path d="M0 14C50 40 100 44 150 30s100-18 149 0V52H0z" fill="var(--mist)"/></svg>
</div>
<div class="card" style="left:446px">
  <div class="badge"><svg width="38" height="34" viewBox="0 0 38 34"><path d="M4 4h14v16H4z" fill="#fff"/><path d="M20 8h6l5 12h-11z" fill="#fff"/><path d="M31 2v24h6" fill="none" stroke="#fff" stroke-width="2.5"/><circle cx="9" cy="26" r="4" fill="#fff"/><circle cx="24" cy="26" r="4" fill="#fff"/></svg></div>
  <h3><b>Freight &amp;</b><br>Logistics Services</h3>
  <p>Sed ut perspiciatis unde omnis iste natus error sit voluptatem accusantium dolore mque laudantium.</p>
  <a class="btn">Read More</a>
  <div class="pic" role="img" aria-label="Workers in hi-vis vests loading a van at a warehouse dock" style="background:linear-gradient(180deg,#2b2a2a 0%,#6b5a44 40%,#c79a5e 60%,#3b3530 100%)"></div>
  <svg class="abs" style="left:0;top:431px" width="299" height="52" viewBox="0 0 299 52"><path d="M0 30C50 10 100 14 150 30s100 18 149 0V52H0z" fill="var(--mist)"/></svg>
</div>
<div class="card" style="left:781px">
  <div class="badge"><svg width="34" height="32" viewBox="0 0 34 32"><path d="M2 10 17 2l15 8v20H2z" fill="#fff"/><rect x="8" y="14" width="18" height="16" fill="var(--blue)"/><path d="M10 18h14M10 22h14M10 26h14" stroke="#fff" stroke-width="2"/></svg></div>
  <h3><b>Warehousing &amp;</b><br>Storage</h3>
  <p>Sed ut perspiciatis unde omnis iste natus error sit voluptatem accusantium dolore mque laudantium.</p>
  <a class="btn">Read More</a>
  <div class="pic" role="img" aria-label="Tall warehouse racking stacked with boxes and a forklift" style="background:linear-gradient(180deg,#5b6a80 0%,#8a7a6a 40%,#c48a4a 60%,#9aa4b0 100%)"></div>
  <svg class="abs" style="left:0;top:431px" width="299" height="52" viewBox="0 0 299 52"><path d="M0 30C50 10 100 14 150 30s100 18 149 0V52H0z" fill="var(--mist)"/></svg>
</div>

<!-- Why choose -->
<h2 class="head abs" style="left:132px;top:2058px;font-size:29px;line-height:45px">Why Choose<br>Garvel Pryce Transport</h2>
<div class="rule" style="left:132px;top:2170px"></div>
<div class="photo" role="img" aria-label="Two lorries on a seaside road under a cloudy blue sky" style="left:132px;top:2218px;width:427px;height:306px;background:linear-gradient(180deg,#4e86c4 0%,#c8d8e8 30%,#5d7aa0 45%,#8a8c90 70%,#5d6a4a 100%)"></div>

<div class="acc" style="top:2070px"><svg class="ic" viewBox="0 0 28 28"><rect x="3" y="9" width="22" height="15" rx="2" fill="var(--blue)"/><path d="M10 9V6h8v3" fill="none" stroke="var(--blue)" stroke-width="2"/></svg>Over 30 Years of Experience<svg class="plus" viewBox="0 0 16 16"><path d="M8 1v14M1 8h14" stroke="var(--ink)" stroke-width="1.6"/></svg></div>
<div class="acc" style="top:2138px"><svg class="ic" viewBox="0 0 28 28"><path d="M14 2 24 6v8c0 6-4 10-10 12C8 24 4 20 4 14V6z" fill="var(--blue)"/><path d="m9 14 4 4 6-7" fill="none" stroke="#fff" stroke-width="2"/></svg>Reliable<svg class="plus" viewBox="0 0 16 16"><path d="M8 1v14M1 8h14" stroke="var(--ink)" stroke-width="1.6"/></svg></div>
<div class="acc" style="top:2206px"><svg class="ic" viewBox="0 0 28 28"><circle cx="14" cy="14" r="11" fill="none" stroke="var(--blue)" stroke-width="2.5"/><path d="M14 8v6l4 3" fill="none" stroke="var(--blue)" stroke-width="2.2"/></svg>24/7 Service<svg class="plus" viewBox="0 0 16 16"><path d="M8 1v14M1 8h14" stroke="var(--ink)" stroke-width="1.6"/></svg></div>
<div class="acc" style="top:2274px"><svg class="ic" viewBox="0 0 28 28"><circle cx="14" cy="14" r="11" fill="var(--blue)"/><path d="M3 14h22M14 3c-5 6-5 16 0 22M14 3c5 6 5 16 0 22" fill="none" stroke="#fff" stroke-width="1.5"/></svg>Work with Global Corporations<svg class="plus" viewBox="0 0 16 16"><path d="M8 1v14M1 8h14" stroke="var(--ink)" stroke-width="1.6"/></svg></div>
<div class="acc" style="top:2342px"><svg class="ic" viewBox="0 0 28 28"><circle cx="14" cy="15" r="10" fill="none" stroke="var(--blue)" stroke-width="2"/><circle cx="14" cy="15" r="5" fill="none" stroke="var(--blue)" stroke-width="2"/><circle cx="14" cy="15" r="1.6" fill="var(--blue)"/></svg>Customer Focused Approach<svg class="plus" viewBox="0 0 16 16"><path d="M8 1v14M1 8h14" stroke="var(--ink)" stroke-width="1.6"/></svg></div>
<div class="acc" style="top:2410px"><svg class="ic" viewBox="0 0 28 28"><path d="M2 8h15v11H2zM17 11h5l4 4v4h-9z" fill="var(--blue)"/><circle cx="7" cy="21" r="2.5" fill="var(--blue)"/><circle cx="21" cy="21" r="2.5" fill="var(--blue)"/></svg>Range of Container Haulage<svg class="plus" viewBox="0 0 16 16"><path d="M8 1v14M1 8h14" stroke="var(--ink)" stroke-width="1.6"/></svg></div>
<div class="acc" style="top:2478px"><svg class="ic" viewBox="0 0 28 28"><path d="M4 2h13l5 5v17H4z" fill="var(--blue)"/><path d="M8 10h9M8 14h9" stroke="#fff" stroke-width="1.8"/><circle cx="20" cy="20" r="6" fill="#fff" stroke="var(--blue)" stroke-width="2"/><path d="m17.5 20 2 2 3-3.5" fill="none" stroke="var(--blue)" stroke-width="1.6"/></svg>Fully Insured<svg class="plus" viewBox="0 0 16 16"><path d="M8 1v14M1 8h14" stroke="var(--ink)" stroke-width="1.6"/></svg></div>

<!-- Fleet -->
<section class="abs" style="left:0;top:2607px;width:1200px;height:530px">
  <div class="abs" style="left:0;top:0;width:606px;height:530px;background:var(--mist)"></div>
  <div class="photo" role="img" aria-label="White and red lorry cab parked at dusk beside trees" style="left:606px;top:0;width:594px;height:530px;background:linear-gradient(180deg,#6f8fb8 0%,#a5b3c4 35%,#4a4f45 55%,#8a8a86 80%,#545a60 100%)"></div>
  <h2 class="head abs" style="left:132px;top:72px;font-size:29px">Our Fleet</h2>
  <div class="rule" style="left:134px;top:133px;width:58px"></div>
  <p class="para abs" style="left:134px;top:183px;width:398px">Sed ut perspiciatis unde omnis iste natus error sit voluptatem accusantium doloremque laudantium, totam rem aperiam, eaque ipsa quae ab illo inventore veritatis et quasi architecto beatae vitae dicta sunt explicabo. Nemo enim ipsam volup tatem quia voluptas sit aspernatur aut odit aut fugit, sed quia consequuntur magni dolores eos qui ratione voluptatem sequi nesciunt. Neque porro quisquam est, qui dolorem ipsum quia dolor sit amet, consectetur, adipisci velit</p>
  <a class="btn" style="left:135px;top:383px;width:133px;height:45px">Read More</a>
</section>

<!-- Footer band -->
<footer class="abs" style="left:0;top:3585px;width:1200px;height:461px;background:linear-gradient(180deg,var(--ruby) 0%,var(--ruby-deep) 100%)">
  <div class="brand" style="left:132px;top:194px;color:#fff"><span class="l1">Garvel Pryce</span><span class="l2">Transport</span></div>

  <div class="ft-h" style="left:448px;top:140px">Contact Us</div>
  <div class="ft-u" style="left:448px;top:166px;width:193px"></div>
  <div class="ft-item" style="left:448px;top:203px"><span class="ft-dot"><svg width="12" height="14" viewBox="0 0 12 14"><path d="M6 0a5 5 0 0 1 5 5c0 4-5 9-5 9S1 9 1 5a5 5 0 0 1 5-5z" fill="var(--ruby)"/><circle cx="6" cy="5" r="1.8" fill="#fff"/></svg></span><span>Hedeby Road 214,<br>4410 Tormark</span></div>
  <div class="ft-item" style="left:448px;top:255px"><span class="ft-dot"><svg width="12" height="12" viewBox="0 0 12 12"><path d="M2.5 1c.6-.3 1.2 0 1.5.6l.8 1.6c.2.5 0 1-.4 1.3l-.6.4c.6 1.3 1.5 2.3 2.8 2.9l.5-.6c.4-.4.9-.5 1.4-.3l1.5.8c.6.4.8 1 .4 1.6-.7 1-1.7 1.4-2.8 1C4.6 9.3 2.4 7 1.6 4 1.3 3 1.7 1.6 2.5 1z" fill="var(--ruby)"/></svg></span><span>Call Us<br>+1 555 014 2290</span></div>
  <div class="ft-item" style="left:448px;top:307px"><span class="ft-dot"><svg width="12" height="10" viewBox="0 0 12 10"><rect x="0.5" y="0.5" width="11" height="9" fill="var(--ruby)"/><path d="m1 1 5 4 5-4" fill="none" stroke="#fff"/></svg></span><span>E mail Us<br>info@garvelprycetransport.com</span></div>

  <div class="ft-h" style="left:745px;top:140px">Menu</div>
  <div class="ft-u" style="left:745px;top:166px;width:106px"></div>
  <div class="menu" style="top:191px">Home<br>About Us<br>Services<br>Team<br>Contact Us</div>

  <div class="ft-h" style="left:958px;top:140px">Follow Us</div>
  <div class="ft-u" style="left:958px;top:166px;width:107px"></div>
  <div class="ft-item" style="left:958px;top:211px"><span class="ft-dot"></span><span>Like us on<br>FRIENDLANE</span></div>
  <div class="ft-item" style="left:958px;top:263px"><span class="ft-dot"></span><span>Follow us on<br>WORKNET</span></div>
  <div class="ft-item" style="left:958px;top:313px"><span class="ft-dot"></span><span>Follow us on<br>SNAPGRAM</span></div>

  <div class="abs" style="left:132px;top:370px;width:936px;height:1px;background:rgba(255,255,255,.45)"></div>
  <div class="abs" style="left:0;width:1200px;top:406px;text-align:center;font-size:11px;color:#fff">Copyright © 2024 All Rights Reserved</div>
</footer>

<!-- Safety banner -->
<section class="abs" style="left:121px;top:3198px;width:952px;height:481px;background:#fff">
  <div class="photo" role="img" aria-label="Two lorries parked side by side at night" style="left:13px;top:11px;width:928px;height:459px;background:linear-gradient(90deg,#151518 0%,#2a2a30 40%,#4a4a4e 65%,#1e1e22 100%)"></div>
  <div class="abs" style="left:13px;top:11px;width:928px;height:459px;background:linear-gradient(90deg,rgba(0,0,0,.55),rgba(0,0,0,0) 50%)"></div>
  <h2 class="head abs" style="left:75px;top:96px;font-size:40px;line-height:42px;color:#fff">We take<br><span style="color:#d0102e">Safety</span> to<br>a whole<br>new level</h2>
  <p class="abs" style="left:75px;top:278px;width:290px;font-size:14px;line-height:20px;color:#fff">Sed ut perspiciatis unde omnis iste natus error sit voluptatem accusantium.</p>
  <a class="btn" style="left:75px;top:338px;width:236px;height:44px;font-size:14px">Our Approach to Safety</a>
</section>

</body>
</html>
```